Taro Reserve website (www.taroreserve.com)

My company develops booking software, Taro Reserve, for the hourly booking of resources such as classes in a school or customer booking involving rooms in a spa. These bookings also involve the customers, staff, rooms and a lesson or treatment.

The main difference between this software and general calendar software such as Plonkit calendar is that this Taro Reserve allows resources such as people and rooms to be associated with the bookings. This is important for example in the case of a Spa to make sure the rooms are booked appropriately and to see the free times for the rooms. For a golf practice range the players much be booked to the tee spots where they practice golf.

I have tried to design the website myself, as a computer programmer- I am a bit "square" and not a designer, my first attempt is http://www.taroreserve.com/, my second attempt is at http://www.lumex-works.com/taroreservewebsite/
I am not happy with my designs as compared to the professional designs I see people can come up with here. The software must have the image of a professional software product in order to inspire the confidence of customers.

Am looking for a design which will be the most likely to give the customer the following feeling:
* Confident the product can do the job.
* Feel easy to want to try it, at least for the free trial.
* Its a professional software product and also a web based product, the user can login from the web.

Look at other booking software websites for ideas, here is a list of links to similar booking products. These products all have different features but are mostly for resource booking.
http://lumex-works.com/taroreservewebsite/?page=compare
Updates

Hello all,

Thankyou for the designs so far, to save peoples time, I will try to eliminate the bottom 50% of designs now.

To be honest, most of the designs are of a good or high quality, I think its very tough on you as graphic and web designers. Only a minor few are of low quality.

If your design is discarded - I would say its unlikely that you are going to be able to produce a design that will beat the competition. 
You probably already know, you could try to re-sell your design later for other projects or as a template on one of those template websites. Some of these discarded designs are quite worthwhile designs.

Best regards, Gordon

Target Market(s)

Spa, Gym, School, Golf, any organization who manages bookings of their customers

Industry/Entity Type

Software

Requirements
Must have
• Home page and inner page, any other pages up to you.

Make a logo or use the image of the girl that I already have on the second design.

Menu(s) for navigation.

A language switcher for 3 languages, English, Chinese Traditional and Chinese Simplified. (Western, Hong Kong and Chinese mainland market are important).

Space for a video introduction, it could be small and when the user clicks on it then it gets bigger then it won't take up too much space. Up to you.

A space for the user to login and register a new account.

Screenshots.

I don't have any strong preferences, use your own ideas, if you look at all the other products you can get the basic idea from them.

The total goal is to make a website which is going to lead to sales of the software product.

```html
<!DOCTYPE html>
<html lang="en">
<head>
<meta charset="utf-8">
<title>Taro Reserve – Bookings</title>
<link href="https://fonts.googleapis.com/css2?family=PT+Sans:wght@400;700&family=Great+Vibes&display=swap" rel="stylesheet">
<style>
:root{
  --bg-edge:#a9d6e2;
  --bg-mid:#e4f3f7;
  --teal:#6cb3c3;
  --teal-dark:#4f9fb2;
  --teal-light:#8fd0de;
  --binder:#2b2b2b;
  --page:#eeeff0;
  --page-line:#cfd3d5;
  --text:#4a4a4a;
  --text-soft:#6d6d6d;
  --link:#2f8aa3;
  --cell:#dfe1e2;
  --cell-mute:#ececec;
  --white:#ffffff;
}
*{box-sizing:border-box;margin:0;padding:0}
html,body{width:1200px;height:900px;overflow:hidden}
body{font-family:"PT Sans",Arial,sans-serif;color:var(--text);
  background:radial-gradient(ellipse 70% 65% at 50% 48%,#ffffff 0%,var(--bg-mid) 60%,var(--bg-edge) 100%);
  position:relative}
.abs{position:absolute}
.top-rule{left:0;top:0;width:1200px;height:3px;background:var(--teal)}
.language{right:32px;top:10px;font-size:14px;color:#5b6b70;display:flex;gap:14px;align-items:center}
.language span{display:flex;align-items:center;gap:4px}
.radio{width:13px;height:13px;border-radius:50%;border:1px solid #aab;background:#fff;display:inline-block;position:relative}
.radio.on::after{content:"";position:absolute;left:3px;top:3px;width:5px;height:5px;border-radius:50%;background:#555}

.binder{left:86px;top:96px;width:1019px;height:731px;background:var(--binder);border-radius:14px;box-shadow:0 4px 12px rgba(0,0,0,.35)}
.page-stack{left:408px;top:126px;width:660px;height:676px;background:#dcdedf;border-radius:0 6px 6px 0;box-shadow:2px 0 0 #c8cacb,4px 0 0 #e2e3e4,6px 0 0 #c8cacb}
.page-left{left:105px;top:123px;width:290px;height:677px;background:var(--page);border-radius:4px 0 0 4px}
.page-right{left:408px;top:123px;width:653px;height:677px;background:linear-gradient(#f3f4f4,#e9eaeb);border-radius:0 4px 4px 0}

.tabs{left:408px;top:86px;display:flex;height:37px}
.tab{position:absolute;top:0;height:37px;background:linear-gradient(var(--teal-light),var(--teal));color:#fff;font-weight:700;font-size:16px;display:flex;align-items:center;justify-content:center;border-radius:3px 3px 0 0}
.tab.active{background:#f2f3f3;color:#3c3c3c;height:38px}

.mascot{left:182px;top:33px;width:111px;height:237px;background:linear-gradient(#b5683a 0%,#f1c39c 35%,#ffffff 55%,#2d2d2d 75%,#f1c39c 100%);border-radius:40px 40px 6px 6px;opacity:.85}
.brand-sign{left:129px;top:147px;width:223px;height:70px;background:#fff;border:1px solid #bbb;box-shadow:0 2px 4px rgba(0,0,0,.2);display:flex;align-items:center;justify-content:center;font-size:28px;color:#555}
.rule{height:1px;background:var(--page-line)}
.client{left:131px;top:308px;width:222px;text-align:center;font-size:18px;font-weight:700;color:#555}
.welcome{left:131px;top:362px;width:222px;text-align:center;font-family:"Great Vibes",cursive;font-size:38px;color:#8a8a8a}
.label{font-size:13px;font-weight:700;color:#555}
.value{font-size:14px;color:var(--text-soft)}
.btn{background:linear-gradient(#fafafa,#dcdcdc);border:1px solid #c4c4c4;border-radius:4px;color:#666;font-size:15px;display:flex;align-items:center;justify-content:center;box-shadow:0 1px 2px rgba(0,0,0,.15)}
.news-head{left:135px;top:606px;font-size:16px;font-weight:700;color:#444}
.news-title{font-size:14px;color:#666}
.news-date{font-size:12px;color:#777}

.rings{left:380px;top:0}

.steps{left:447px;top:145px;width:580px;height:47px;background:#fbfbfb;border:1px solid #dcdcdc;box-shadow:0 1px 3px rgba(0,0,0,.12)}
.step{position:absolute;top:0;height:47px;display:flex;align-items:center;justify-content:center;font-size:15px;color:#8d8d8d;width:145px}
.step.current{color:#444;font-weight:400;background:#eeeeee}
.heading{font-size:16px;font-weight:700;color:#555}

.calendar{left:463px;top:316px;width:237px;background:#e8e9ea;box-shadow:0 2px 4px rgba(0,0,0,.3)}
.cal-head{height:38px;background:#333;color:#fff;display:flex;align-items:center;justify-content:space-between;padding:0 12px;font-size:17px}
.cal-grid{display:grid;grid-template-columns:repeat(7,1fr)}
.dow{height:20px;font-size:9px;color:#555;display:flex;align-items:center;justify-content:center;font-weight:700;background:#ededed;border-right:1px solid #ddd}
.day{height:34px;display:flex;align-items:center;justify-content:center;font-size:15px;font-weight:700;color:#555;background:linear-gradient(#e9eaea,#d6d8d9);border-right:1px solid #c9cbcc;border-bottom:1px solid #c9cbcc}
.day.mute{color:#b5b5b5;background:var(--cell-mute);font-weight:400}
.day.sel{background:var(--teal-dark);color:#a8dce7}

.slot{width:134px;height:40px;border:1px solid #c9d3d6;border-radius:3px;background:linear-gradient(#ffffff,#eceded);font-size:15px;color:#555;display:flex;align-items:center;justify-content:center}
.slot.on{background:linear-gradient(var(--teal-light),#5fb3c6);color:#fff;border-color:#7fc3d1}

.pick{left:467px;font-size:15px;color:var(--link);display:flex;align-items:center;gap:8px;font-weight:700}
.pick svg{width:15px;height:15px}

.footer{left:0;top:861px;width:1200px;height:39px;background:var(--teal);display:flex;align-items:center;color:#fff;font-size:14px;font-weight:700}
.footer nav{display:flex;gap:0;margin-left:104px}
.footer nav a{color:#fff;text-decoration:none;margin-right:28px}
.footer .copy{position:absolute;right:102px;color:#d8eef3}
</style>
</head>
<body>
<div class="abs top-rule"></div>

<div class="abs language">
  <span>Language:</span>
  <span><i class="radio on"></i>English</span>
  <span><i class="radio"></i>体体</span>
  <span><i class="radio"></i>繁體</span>
</div>

<div class="abs binder"></div>
<div class="abs page-stack"></div>

<nav class="abs tabs">
  <div class="tab" style="left:0;width:92px">About</div>
  <div class="tab active" style="left:98px;width:93px">Bookings</div>
  <div class="tab" style="left:192px;width:91px">Free Trial</div>
  <div class="tab" style="left:288px;width:137px">Documentation</div>
  <div class="tab" style="left:431px;width:94px">Purchase</div>
  <div class="tab" style="left:531px;width:94px">Compare</div>
</nav>

<aside class="abs page-left"></aside>
<div class="abs mascot" role="img" aria-label="Brand mascot illustration: cartoon woman holding the name sign"></div>
<div class="abs brand-sign">Taro Reserve</div>

<div class="abs rule" style="left:131px;top:291px;width:222px"></div>
<div class="abs client">The Calm Spa Group</div>
<div class="abs rule" style="left:131px;top:348px;width:222px"></div>
<div class="abs welcome">Welcome Back!</div>
<div class="abs rule" style="left:131px;top:418px;width:222px"></div>

<div class="abs label" style="left:143px;top:433px">Website:</div>
<div class="abs value" style="left:143px;top:450px">www.calmspagroup.com</div>
<div class="abs label" style="left:143px;top:483px">Email:</div>
<div class="abs value" style="left:143px;top:500px">info@calmspagroup.com</div>
<div class="abs label" style="left:143px;top:530px">Phone:</div>
<div class="abs value" style="left:143px;top:547px">+27 555 0192</div>
<div class="abs btn" style="left:260px;top:540px;width:92px;height:31px">Sign Out</div>
<div class="abs rule" style="left:131px;top:587px;width:222px"></div>

<div class="abs news-head">Latest News</div>
<div class="abs news-title" style="left:136px;top:638px">News title goes here</div>
<div class="abs news-date" style="left:136px;top:657px">31 October 2011</div>
<div class="abs news-title" style="left:136px;top:691px">News title goes here</div>
<div class="abs news-date" style="left:136px;top:710px">29 October 2011</div>
<div class="abs news-title" style="left:136px;top:744px">News title goes here</div>
<div class="abs news-date" style="left:136px;top:763px">8 October, 2011</div>

<main class="abs page-right"></main>

<svg class="abs rings" width="42" height="800" viewBox="0 0 42 800" aria-hidden="true">
  <g fill="none" stroke="#222" stroke-width="3">
    <g id="pair">
      <rect x="2" y="-6" width="38" height="11" rx="5.5" fill="#f2f2f2"/>
      <rect x="2" y="9" width="38" height="11" rx="5.5" fill="#f2f2f2"/>
    </g>
  </g>
  <use href="#pair" y="0" transform="translate(0,183)"/>
  <use href="#pair" transform="translate(0,236)"/>
  <use href="#pair" transform="translate(0,289)"/>
  <use href="#pair" transform="translate(0,412)"/>
  <use href="#pair" transform="translate(0,465)"/>
  <use href="#pair" transform="translate(0,518)"/>
  <use href="#pair" transform="translate(0,647)"/>
  <use href="#pair" transform="translate(0,700)"/>
  <use href="#pair" transform="translate(0,753)"/>
</svg>
<svg class="abs" style="left:0;top:0" width="1" height="1" aria-hidden="true"></svg>

<div class="abs steps">
  <div class="step" style="left:0">1. Details</div>
  <div class="step current" style="left:145px">2. Date &amp; Time</div>
  <div class="step" style="left:290px">3. Schedule</div>
  <div class="step" style="left:435px">4. Confirm</div>
  <svg class="abs" style="left:0;top:0" width="580" height="47" aria-hidden="true">
    <g fill="none" stroke="#d3d3d3" stroke-width="1.5">
      <polyline points="135,0 155,23.5 135,47"/>
      <polyline points="280,0 300,23.5 280,47"/>
      <polyline points="425,0 445,23.5 425,47"/>
    </g>
  </svg>
</div>

<div class="abs rule" style="left:462px;top:214px;width:552px"></div>
<div class="abs heading" style="left:462px;top:236px">Please select 3 different time slots that suit you:</div>
<div class="abs rule" style="left:462px;top:274px;width:552px"></div>

<section class="abs calendar" aria-label="Calendar November 2011">
  <div class="cal-head"><span style="font-size:11px">◀</span><span>November 2011</span><span style="font-size:11px">▶</span></div>
  <div class="cal-grid">
    <div class="dow">MON</div><div class="dow">TUE</div><div class="dow">WED</div><div class="dow">THU</div><div class="dow">FRI</div><div class="dow">SAT</div><div class="dow">SUN</div>
    <div class="day mute">28</div><div class="day">1</div><div class="day">2</div><div class="day">3</div><div class="day sel">4</div><div class="day">5</div><div class="day">6</div>
    <div class="day">7</div><div class="day">8</div><div class="day">9</div><div class="day">10</div><div class="day">11</div><div class="day">12</div><div class="day">13</div>
    <div class="day">14</div><div class="day">15</div><div class="day">16</div><div class="day">17</div><div class="day">18</div><div class="day">19</div><div class="day">20</div>
    <div class="day">21</div><div class="day">22</div><div class="day">23</div><div class="day">24</div><div class="day">25</div><div class="day">26</div><div class="day">27</div>
    <div class="day">28</div><div class="day">29</div><div class="day">30</div><div class="day">31</div><div class="day mute">1</div><div class="day mute">2</div><div class="day mute">3</div>
  </div>
</section>

<div class="abs slot on" style="left:730px;top:328px">9:00 am</div>
<div class="abs slot" style="left:879px;top:328px">1:00 pm</div>
<div class="abs slot on" style="left:730px;top:382px">10:00 am</div>
<div class="abs slot" style="left:879px;top:382px">2:00 pm</div>
<div class="abs slot" style="left:730px;top:436px">11:00 am</div>
<div class="abs slot on" style="left:879px;top:436px">3:00 pm</div>
<div class="abs slot" style="left:730px;top:490px">12:00 pm</div>
<div class="abs slot" style="left:879px;top:490px">4:00 pm</div>

<div class="abs rule" style="left:462px;top:591px;width:552px"></div>
<div class="abs heading" style="left:464px;top:611px">Selected Dates &amp; Times:</div>
<div class="abs rule" style="left:462px;top:647px;width:552px"></div>

<div class="abs pick" style="top:670px">
  <svg viewBox="0 0 15 15"><rect x=".5" y=".5" width="14" height="14" rx="2" fill="#fff" stroke="#9aa"/><path d="M3 7.5l3 3 6-7" fill="none" stroke="#3a8fa6" stroke-width="2.2"/></svg>
  4 Nov 2011 - 9:00 am (1 hour)
</div>
<div class="abs pick" style="top:696px">
  <svg viewBox="0 0 15 15"><rect x=".5" y=".5" width="14" height="14" rx="2" fill="#fff" stroke="#9aa"/><path d="M3 7.5l3 3 6-7" fill="none" stroke="#3a8fa6" stroke-width="2.2"/></svg>
  4 Nov 2011 - 10:00 am (1 hour)
</div>
<div class="abs pick" style="top:723px">
  <svg viewBox="0 0 15 15"><rect x=".5" y=".5" width="14" height="14" rx="2" fill="#fff" stroke="#9aa"/><path d="M3 7.5l3 3 6-7" fill="none" stroke="#3a8fa6" stroke-width="2.2"/></svg>
  4 Nov 2011 - 3:00 pm (1 hour)
</div>
<div class="abs btn" style="left:920px;top:727px;width:91px;height:30px">next...</div>
<div class="abs rule" style="left:462px;top:768px;width:552px"></div>

<footer class="abs footer">
  <nav>
    <a href="#">About</a><a href="#">Events</a><a href="#">Press</a><a href="#">Jobs</a><a href="#">Staff</a><a href="#">Resources</a><a href="#">Privacy</a><a href="#">T&amp;Cs</a><a href="#">Feedback</a><a href="#">Customer Service</a><a href="#">Contact</a>
  </nav>
  <span class="copy">© 2011 Taro Reserve</span>
</footer>
</body>
</html>
```